Quorva - corporate Business Card

We need a good look and innovative business card for a new start up company based in Los Angeles called "Quorva". We are in a payment business, including payment card, app, and ewallet. We are expert in online payment and Card not present (CNP) transaction.
We need an innovative, modern business card.

Our logo font is Aero Matics

Target Market(s)

Startup - Bank - Online Payment - Card Manufacturing

Industry/Entity Type

Startup

Contact Information for Business Card

phone: 555 014 7396 - Address: 4172 Marlowe blvd, Ashmere Vale, NV 89201

Requirements
Must have
• Message: innovative, professional, expert, high tech, trust, online payment expert, security
Nice to have
• no comment
Should not have
• no Comment

```html
<!DOCTYPE html>
<html lang="en">
<head>
<meta charset="utf-8">
<title>Quorva Business Card</title>
<link rel="stylesheet" href="https://fonts.googleapis.com/css2?family=Roboto:wght@300;400;500&display=swap">
<style>
  :root {
    --brand-red: #b71c2e;
    --brand-red-light: #cf3446;
    --card-white: #ffffff;
    --ink: #4a4a4a;
    --ink-soft: #8a8a8a;
    --rule: #9a9a9a;
    --backdrop: #e6e6e8;
  }
  * { margin: 0; padding: 0; box-sizing: border-box; }
  html, body {
    width: 1200px; height: 950px; overflow: hidden;
    background: var(--backdrop);
    font-family: "Roboto", Arial, sans-serif;
  }
  .sheet {
    width: 1200px; height: 950px;
    display: flex; flex-direction: column;
    align-items: center; justify-content: center; gap: 50px;
  }
  .card {
    position: relative; width: 700px; height: 400px; overflow: hidden;
    box-shadow: 0 6px 18px rgba(0,0,0,0.18);
  }
  .card-front { background: var(--card-white); }
  .card-back { background: var(--brand-red); }

  .front-swoosh { position: absolute; inset: 0; width: 700px; height: 400px; }

  .brand {
    position: absolute; display: flex; align-items: center; gap: 14px;
    font-weight: 500; line-height: 1;
  }
  .brand-dot { border-radius: 50%; flex: none; }
  .brand-front { left: 235px; top: 52px; color: var(--brand-red); font-size: 64px; }
  .brand-front .brand-dot { width: 62px; height: 62px; background: var(--brand-red); }

  .front-rule {
    position: absolute; left: 190px; right: 52px; top: 178px;
    height: 1px; background: var(--rule);
  }

  .person { position: absolute; left: 190px; top: 236px; }
  .person-name { color: var(--brand-red); font-size: 24px; font-weight: 400; }
  .person-role { color: var(--ink-soft); font-size: 17px; font-weight: 300; margin-top: 2px; }

  .contact-list { list-style: none; margin-top: 12px; }
  .contact-list li {
    display: flex; align-items: center; gap: 10px;
    color: var(--ink); font-size: 16px; font-weight: 300; line-height: 24px;
  }
  .contact-icon { width: 14px; height: 14px; flex: none; }

  .address {
    position: absolute; right: 52px; top: 198px; text-align: right;
    color: var(--ink); font-size: 17px; font-weight: 300; line-height: 24px;
    font-style: normal;
  }

  .brand-back { left: 190px; top: 160px; color: var(--card-white); font-size: 88px; }
  .brand-back .brand-dot { width: 88px; height: 88px; background: var(--card-white); }

  .web-address {
    position: absolute; left: 230px; top: 92px;
    color: var(--card-white); font-size: 15px; font-weight: 300; letter-spacing: 6px;
  }
</style>
</head>
<body>
<main class="sheet">
  <section class="card card-front" aria-label="Business card front">
    <svg class="front-swoosh" viewBox="0 0 700 400" aria-hidden="true">
      <path d="M0 0 H118 C60 150 95 315 290 400 H0 Z" fill="var(--brand-red)"/>
      <path d="M0 0 H92 C40 150 72 300 230 400 H0 Z" fill="var(--brand-red-light)" opacity="0.45"/>
    </svg>

    <div class="brand brand-front">
      <span class="brand-dot"></span>
      <span class="brand-name">quorva</span>
    </div>

    <div class="front-rule"></div>

    <div class="person">
      <p class="person-name">Mara Lindqvist</p>
      <p class="person-role">President</p>
      <ul class="contact-list">
        <li>
          <svg class="contact-icon" viewBox="0 0 16 16" aria-hidden="true"><path d="M4 1 L6.5 4.5 L5 6.5 C6 8.5 7.5 10 9.5 11 L11.5 9.5 L15 12 L13.5 15 C7 14.5 1.5 9 1 2.5 Z" fill="var(--brand-red)"/></svg>
          555 014 7396
        </li>
        <li>
          <svg class="contact-icon" viewBox="0 0 16 16" aria-hidden="true"><rect x="1" y="3" width="14" height="10" fill="var(--brand-red)"/><path d="M1 3 L8 9 L15 3" fill="none" stroke="#fff" stroke-width="1.4"/></svg>
          mara@quorva.com
        </li>
        <li>
          <svg class="contact-icon" viewBox="0 0 16 16" aria-hidden="true"><circle cx="8" cy="8" r="7.5" fill="var(--brand-red)"/><circle cx="8" cy="8" r="4.5" fill="none" stroke="#fff" stroke-width="1.2"/><path d="M3.5 8 H12.5 M8 3.5 V12.5" stroke="#fff" stroke-width="1.2"/></svg>
          www.quorva.com
        </li>
      </ul>
    </div>

    <address class="address">
      4172 Marlowe blvd<br>
      Ashmere Vale, NV 89201
    </address>
  </section>

  <section class="card card-back" aria-label="Business card back">
    <p class="web-address">www.quorva.com</p>
    <div class="brand brand-back">
      <span class="brand-dot"></span>
      <span class="brand-name">quorva</span>
    </div>
  </section>
</main>
</body>
</html>
```